Store Front Window Design

We have a beautiful corner store front dental practice with no window signage. Crazy I know...that's why we need your help.

The final design will be done in all vinyl unless unless you suggest a different medium (meaning we are open to some design idea like using frosted glass, etc...).

The windows provide a lot of natural light so the design needs to keep a lot of natural light coming into the office. Keep in mind vinyl is not opaque so keep the signage aesthetically pleasing and a minimalist design to allow as much natural light in as possible. The design should follow the aesthetic from our logo. or tie into at least. We want a cohesive brand aesthetic.

I submitted some general layout ideas. There is a blue banner with advertising words which we want to be used in the final version. Even though the lettering is black, in reality the letters will be a white vinyl on the outside of the window. When you submit your work, be sure to add any special instructions (aka tell me the vision for the letters is white not black, maybe gold leaf, or forested glass...stuff like that). AND YOU DO NOT HAVE TO FOLLOW MY PATTERN! YOU ARE ARTISTS AND WE ARE LOOKING FOR AN ARTISTIC EYE CATCHING PRESENTATION OF THIS INFORMATION. MAKE IT FLASHY AND ADD SOME AESTHETIC FROM THE TOOTH LOGO.

The store front is 6 windows roughly 60'' x 36'' The smaller windows below are 27'' x 36''. Around the corner there are 3 windows. they are 60'' x 27'' lower windows are 27" x 27". We would like to keep the bottom windows clear and keep the signage on the top windows, however, we are flexible.

The front 6 windows need to have this information worked into the design.

Practice name: Varden and Pellosi Dental & Orthodontics.
Phone numbers: Rosalind Varden DDS: 415.555.0187
Oskar Pellosi DDS:415.555.0243

Expertise: Dr. Varden General Dentistry & Orthodontics
Dr. Pellosi Oral Surgery & Sedation

Address: 1938 Birchwood Ave

A banner across the bottom of the top windows with some key advertisement words: "Clearmold" "Braces" "Implants" "Whiting" "Call today" "Free Consultation" "Oral Surgery" "Sedation". We like the two color idea. Its up to you to decide on the color combo. I used a Dark and light blue, but maybe a Blue and grey would nice to tire in the logo colors?

I have made some mock ideas to get the ball rolling but you do not have to stick to these designs at all, just as long as all the required information is there. Be creative with the layouts, fonts, color scheme, (just remember these are going on windows not necessarily a white background), and graphics/artistic flare (refer to logo for layout inspiration and use the logo as an actual graphic). We are running a miltimillion dollar dental practice so we want these windows to be eye catching to pull in patients and look like a million dollar design. Also all 6 windows dont need ot be used. I am really looking for creative design marketing.

The corner 3 windows need the following information: name, expertise, phone number, banner.

Dr. Varden, General Dentistry & Orthodontics, 415.555.0187
Dr. Pellosi, Oral Surgery & Sedation, 415.555.0243

There is also a front door that needs to be designed. The door is 60'' x 36'' (standard door size) We want simple white vinyl on the outside of the door. We need you to organize the information on the door, pick a easy to read font, maybe use the logo and use some of the front window signage aesthetic? Its up to you...but we we were initially thinking of just making the litters white and keep it simple but again you are the designers.

Practice name: Varden and Pellosi General Dentistry & Orthodontics

Address: 1938 Birchwood Ave

Phone numbers: Dr. Varden 415.555.0187
Dr. Pellosi 415.555.0243

Hours of operation: Mon: call for an appointment
Tues-Thurs: 9am-5pm
Sat: call for an appointment
Sun: Closed

A line saying we speak Spanish: Se Habla Espanol

*****************************************************************************************************
here are some design that we liked and some rough sketches I made to start the ball rolling. Keep in mind that there are 9 windows for the front because its a corner office, but not all of them have to have stuff on it. We want simple, streamline, classy high commanding price point aesthetic. I am hiring you for your artistic minds.

Target Market(s)

anyone who has dental needs

Industry/Entity Type

Dental

Font styles to use
Serif
Sans Serif

Colors

Designer to choose colors to be used in the design.

Requirements
Must have
• 1. The required information (see project description)
• 2. Logo
• 3. Advertisement banner running along the bottom of all 9 windows (6 in front and 3 on the side)
• NOTE: Look at pictures of the store to get a sense of the customers point of view and also as a reference to how your design will be broken up across several windows or maybe you design something special for every window. But we want the banner to run along all the windows to lead customs to the door on the side. Finally the letters will be done in white vinyl unless state otherwise, remember the window needs to let in natural light so the entire window can not be covered in vinyl.
Nice to have
• artistic flare yet simple and sleep and expensive looking aesthetic. work logo into the design.
Should not have
• The goal is to catch someone eye and give them important information about the practice.
• It should not just be words.
• It should not have to many words
• It must be readable font for cards driving by.

```html
<!DOCTYPE html>
<html lang="en">
<head>
<meta charset="utf-8">
<title>Varden and Pellosi Dental &amp; Orthodontics — Storefront Windows</title>
<link rel="stylesheet" href="https://fonts.googleapis.com/css2?family=Play:wght@400;700&family=Questrial&display=swap">
<style>
  :root {
    --paper: #ffffff;
    --trim: #f2a7d8;
    --frame: #3a3a3a;
    --brand-blue: #1f74c0;
    --band-blue: #0b5ea8;
    --band-grey: #cbcbcb;
    --panel-grey: #cfcfcf;
    --ink: #111111;
    --divider: #e6e6e6;
  }
  * { box-sizing: border-box; margin: 0; padding: 0; }
  html, body { width: 1200px; height: 743px; overflow: hidden; background: var(--paper); }
  .canvas {
    position: relative; width: 1200px; height: 743px;
    border: 1px solid var(--trim); background: var(--paper);
    font-family: "Play", sans-serif; color: var(--brand-blue);
  }
  .abs { position: absolute; }

  /* logo graphic area */
  .logo-art {
    background: linear-gradient(180deg, rgba(190,190,190,.55) 0%, rgba(205,205,205,.45) 45%, rgba(31,116,192,.35) 60%, rgba(225,225,225,.35) 100%);
    border-radius: 40% 40% 30% 30%;
  }
  .logo-art--left { left: 97px; top: 262px; width: 86px; height: 225px; border-radius: 0 60% 40% 0; }
  .logo-art--center { left: 370px; top: 240px; width: 288px; height: 268px; }

  /* window frames */
  .pane { top: 227px; height: 197px; border: 1px solid var(--frame); }

  /* banner */
  .band-line { height: 4px; background: var(--band-blue); top: 426px; }
  .band-grey { height: 72px; background: var(--band-grey); top: 430px; }
  .band-base { height: 14px; background: var(--band-blue); top: 502px; }
  .band-divider { top: 430px; width: 1px; height: 86px; background: var(--divider); }
  .left-group { left: 97px; width: 271px; }
  .right-group { left: 373px; width: 730px; }

  .banner-word {
    top: 430px; height: 72px; display: flex; align-items: center; justify-content: center;
    font-size: 17px; color: var(--brand-blue); white-space: nowrap;
  }
  .banner-call { left: 97px; width: 271px; font-size: 19px; padding-left: 14px; }

  /* practice name */
  .practice-name { left: 680px; top: 266px; }
  .practice-name__partners {
    font-family: "Questrial", sans-serif; font-size: 19px; letter-spacing: 9.6px;
    color: var(--brand-blue); line-height: 22px;
  }
  .practice-name__title {
    font-family: "Questrial", sans-serif; font-size: 27px; color: var(--ink);
    line-height: 30px; margin-top: 3px; letter-spacing: .3px;
  }
  .practice-name__amp { font-size: 18px; }

  /* info tiles */
  .tile {
    background: var(--panel-grey); color: var(--brand-blue);
    display: flex; flex-direction: column; align-items: center; justify-content: center;
    text-align: center; line-height: 1.1;
  }
  .tile--lg { top: 358px; height: 45px; font-size: 12.5px; }
  .tile--lg .tile__small { font-size: 6px; line-height: 8px; }
  .tile--sm-name { top: 337px; height: 21px; font-size: 7.5px; font-weight: 700; }
  .tile--sm-info { top: 362px; height: 41px; font-size: 7.5px; font-weight: 700; }
  .tile--sm-info .tile__phone { font-size: 10px; font-weight: 400; margin-top: 3px; }
  .tile--sm-info .tile__small { font-size: 5px; line-height: 6px; }
</style>
</head>
<body>
<div class="canvas">

  <div class="abs logo-art logo-art--left" role="img" aria-label="Tooth logo swoosh decoration with braces, continuing from the main mark"></div>
  <div class="abs logo-art logo-art--center" role="img" aria-label="Large faint tooth logo with blue swoosh, braces and implant post"></div>

  <!-- window panes -->
  <div class="abs pane" style="left:97px;width:89px"></div>
  <div class="abs pane" style="left:188px;width:89px"></div>
  <div class="abs pane" style="left:279px;width:89px"></div>
  <div class="abs pane" style="left:372px;width:120px"></div>
  <div class="abs pane" style="left:495px;width:119px"></div>
  <div class="abs pane" style="left:617px;width:119px"></div>
  <div class="abs pane" style="left:739px;width:119px"></div>
  <div class="abs pane" style="left:862px;width:119px"></div>
  <div class="abs pane" style="left:984px;width:119px"></div>

  <!-- banner -->
  <div class="abs band-line left-group"></div>
  <div class="abs band-grey left-group"></div>
  <div class="abs band-base left-group"></div>
  <div class="abs band-line right-group"></div>
  <div class="abs band-grey right-group"></div>
  <div class="abs band-base right-group"></div>

  <div class="abs band-divider" style="left:187px"></div>
  <div class="abs band-divider" style="left:278px"></div>
  <div class="abs band-divider" style="left:494px"></div>
  <div class="abs band-divider" style="left:615px"></div>
  <div class="abs band-divider" style="left:738px"></div>
  <div class="abs band-divider" style="left:860px"></div>
  <div class="abs band-divider" style="left:983px"></div>

  <div class="abs banner-word banner-call">Call today Free Consultation</div>
  <div class="abs banner-word" style="left:617px;width:122px">CLEARMOLD</div>
  <div class="abs banner-word" style="left:739px;width:122px">BRACES</div>
  <div class="abs banner-word" style="left:862px;width:122px">IMPLANTS</div>
  <div class="abs banner-word" style="left:984px;width:119px">WHITENING</div>

  <!-- practice name -->
  <div class="abs practice-name">
    <div class="practice-name__partners">VARDEN AND PELLOSI</div>
    <div class="practice-name__title">DENTAL <span class="practice-name__amp">&amp;</span> ORTHODONTICS</div>
  </div>

  <!-- front info tiles -->
  <div class="abs tile tile--lg" style="left:647px;width:89px">Dentistry<span class="tile__small">&amp;</span>Orthodontics</div>
  <div class="abs tile tile--lg" style="left:739px;width:92px">Rosalind Varden<span class="tile__small">DDS</span>415.555.0187</div>
  <div class="abs tile tile--lg" style="left:892px;width:89px">Oral Surgery<span class="tile__small">&amp;</span>Sedation</div>
  <div class="abs tile tile--lg" style="left:984px;width:92px">Oskar Pellosi<span class="tile__small">DDS</span>415.555.0243</div>

  <!-- corner info tiles -->
  <div class="abs tile tile--sm-name" style="left:198px;width:80px">Dr. Oskar Pellosi<br>D.D.S.</div>
  <div class="abs tile tile--sm-name" style="left:280px;width:77px">Rosalind Varden<br>D.D.S.</div>
  <div class="abs tile tile--sm-info" style="left:198px;width:80px">Oral Surgery<span class="tile__small">&amp;</span>Sedation<span class="tile__phone">415.555.0243</span></div>
  <div class="abs tile tile--sm-info" style="left:280px;width:77px">General Dentistry<span class="tile__small">&amp;</span>Orthodontics<span class="tile__phone">415.555.0187</span></div>

</div>
</body>
</html>
```